Business Card Design

We like to use greens as you will see in our logo (but not TOO much green). We are a Dental Clinic in a somewhat eccentric community. We do not like the dated sharp designs which we see many dentists use. We're looking for something bright and fresh while still maintaining the integrity of the profession. Elegance is not necessarily what we are going for... we need for the design to be "mature" but also up-lifting.

See our logo.
Updates

Project Deadline Extended
Reason: We have 5 designs which we like. But we'd like to see a few more before committing to a design.

Project Deadline Extended
Reason: We are awaiting revisions to this project. We are still welcoming designs while we wait to see if designers are able to provide to us the revisions we require in order to proceed with a selection.

Target Market(s)

Younger families - ages late 20's to early 40's

Industry/Entity Type

Business

Contact Information for Business Card

Corwel T. Banfry DDS 2730 W. Halvert Rd. Ste. 7 Royal Oak, MI 48391 (248)555-0174 FX (248)555-0189 info@BrightwellDentalCareMi.com BrigthwellDentalCareMi.com on the back of the card we need an appointment reminder (For____ Date___ Time____) with "If you are unable to keep your appointment, kindly give 48 hours notice" at the bottom. No use of teeth in the design. DOUBLE SIDED DESIGN

Requirements
Should not have
• The use of pictures of teeth

```html
<!DOCTYPE html>
<html lang="en">
<head>
<meta charset="utf-8">
<title>Brightwell Dental Care – Business Card</title>
<link rel="stylesheet" href="https://fonts.googleapis.com/css2?family=Arimo:wght@400;700&family=Cinzel:wght@500&family=Open+Sans:ital,wght@0,400;0,700;1,600&display=swap">
<style>
  :root {
    --green-dark: #1b6b3a;
    --green-mid: #2e9a49;
    --green-light: #7cc242;
    --ink: #2b2b2b;
    --ink-soft: #3a3a3a;
    --paper: #ffffff;
    --backdrop: #ecebe7;
    --rule: #555555;
  }
  * { box-sizing: border-box; margin: 0; padding: 0; }
  html, body { width: 1200px; height: 1161px; overflow: hidden; }
  body { background: var(--backdrop); position: relative; font-family: "Arimo", Arial, sans-serif; color: var(--ink); }

  .card { position: absolute; background: var(--paper); border-radius: 30px; overflow: hidden; box-shadow: 0 2px 6px rgba(0,0,0,.18); }
  .card--front { left: 30px; top: 48px; width: 913px; height: 520px; }
  .card--back  { left: 243px; top: 613px; width: 910px; height: 521px; border: 1px solid #999; }

  /* Front */
  .doctor-name { position: absolute; left: 62px; top: 66px; font-size: 32px; font-weight: 700; color: var(--green-dark); }
  .doctor-name .credential { font-size: 22px; color: var(--ink-soft); }
  .address { position: absolute; left: 62px; top: 160px; font-size: 23px; line-height: 32px; color: var(--ink); }
  .contact-list { position: absolute; left: 62px; top: 292px; list-style: none; font-size: 23px; }
  .contact-list li { height: 42px; display: flex; align-items: center; gap: 10px; }
  .contact-list svg { width: 20px; height: 20px; fill: var(--ink-soft); }
  .band { position: absolute; top: 444px; height: 17px; }
  .band--dark { left: 0; width: 411px; background: var(--green-dark); }
  .band--light { left: 425px; right: 0; background: var(--green-light); }
  .website { position: absolute; left: 62px; top: 476px; font-size: 22px; letter-spacing: 1.5px; color: var(--ink); }

  .brand { position: absolute; display: flex; align-items: center; gap: 14px; color: var(--green-dark); font-family: "Arimo", Arial, sans-serif; font-weight: 700; }
  .brand__dot { border-radius: 50%; background: var(--green-mid); flex: none; }
  .brand__name { line-height: 1.05; }
  .card--front .brand { left: 500px; top: 150px; font-size: 46px; }
  .card--front .brand__dot { width: 40px; height: 40px; }
  .card--back .brand { left: 630px; top: 40px; font-size: 31px; }
  .card--back .brand__dot { width: 28px; height: 28px; }

  /* Back */
  .appt-title { position: absolute; left: 72px; top: 100px; font-family: "Cinzel", Georgia, serif; font-weight: 500; font-size: 31px; color: var(--green-dark); letter-spacing: .5px; }
  .field { position: absolute; font-family: "Open Sans", Arial, sans-serif; font-size: 24px; color: var(--ink-soft); }
  .fill-line { position: absolute; border-bottom: 2px dotted var(--rule); height: 0; }
  .slot { position: absolute; top: 308px; height: 34px; border: 2px solid #666; border-radius: 4px; }

  .days { position: absolute; left: 0; right: 0; top: 363px; height: 74px; display: flex; }
  .days__weekday { width: 722px; background: var(--green-dark); }
  .days__weekend { flex: 1; margin-left: 3px; background: var(--green-mid); }
  .day { position: absolute; top: 388px; font-family: "Open Sans", Arial, sans-serif; font-weight: 700; font-size: 24px; color: var(--paper); }
  .day-box { position: absolute; top: 383px; height: 34px; background: var(--paper); border: 1px solid #444; border-radius: 5px; }
  .notice { position: absolute; left: 72px; top: 458px; font-family: "Open Sans", Arial, sans-serif; font-style: italic; font-weight: 600; font-size: 23px; color: var(--ink); }
</style>
</head>
<body>

<section class="card card--front" aria-label="Business card front">
  <h1 class="doctor-name">Corwel T. Banfry, <span class="credential">DDS</span></h1>
  <p class="address">2730 W. Halvert Rd.<br>Ste. 7 Royal Oak, MI 48391</p>
  <ul class="contact-list">
    <li><svg viewBox="0 0 20 20"><path d="M5 2l3 4-2 2c1 2 3 4 5 5l2-2 4 3-2 3C9 17 3 11 2 4z"/></svg>(248) 555-0174</li>
    <li><svg viewBox="0 0 20 20"><rect x="5" y="2" width="10" height="6"/><rect x="2" y="8" width="16" height="7" rx="1"/><rect x="5" y="13" width="10" height="5"/></svg>(248) 555-0189</li>
    <li><svg viewBox="0 0 20 20"><path d="M2 8l8-5 8 5v9H2z"/><path d="M3 9l7 5 7-5" fill="none" stroke="#fff" stroke-width="1.5"/></svg>info@BrightwellDentalCareMi.com</li>
  </ul>
  <div class="band band--dark"></div>
  <div class="band band--light"></div>
  <p class="website">www.BrigthwellDentalCareMi.com</p>

  <div class="brand">
    <span class="brand__dot"></span>
    <span class="brand__name">Brightwell<br>Dental Care</span>
  </div>
</section>

<section class="card card--back" aria-label="Appointment card back">
  <div class="brand">
    <span class="brand__dot"></span>
    <span class="brand__name">Brightwell<br>Dental Care</span>
  </div>
  <h2 class="appt-title">YOUR APPOINTMENT</h2>

  <span class="field" style="left:80px; top:180px;">Name :</span>
  <span class="fill-line" style="left:181px; width:661px; top:205px;"></span>

  <span class="field" style="left:80px; top:244px;">Date :</span>
  <span class="fill-line" style="left:181px; width:225px; top:269px;"></span>
  <span class="field" style="left:413px; top:244px;">Time :</span>
  <span class="fill-line" style="left:497px; width:243px; top:269px;"></span>
  <span class="field" style="left:745px; top:244px;">am / pm</span>

  <span class="field" style="left:80px; top:309px;">Next Appointment</span>
  <span class="slot" style="left:327px; width:163px;"></span>
  <span class="slot" style="left:504px; width:164px;"></span>
  <span class="slot" style="left:678px; width:162px;"></span>

  <div class="days"><div class="days__weekday"></div><div class="days__weekend"></div></div>
  <span class="day" style="left:80px;">MON</span><span class="day-box" style="left:158px; width:55px;"></span>
  <span class="day" style="left:225px;">TUE</span><span class="day-box" style="left:290px; width:55px;"></span>
  <span class="day" style="left:357px;">WED</span><span class="day-box" style="left:431px; width:55px;"></span>
  <span class="day" style="left:500px;">THU</span><span class="day-box" style="left:567px; width:56px;"></span>
  <span class="day" style="left:636px;">FRI</span><span class="day-box" style="left:689px; width:55px;"></span>
  <span class="day" style="left:757px;">SAT</span><span class="day-box" style="left:817px; width:56px;"></span>

  <p class="notice">If you are unable to keep your appointment, kindly give 48 hours notice</p>
</section>

</body>
</html>
```